Lev Marchetti - Senior Living Audio CDs - CD Design and Cover Design

I am an executive director in an assisted living facility. I have just started speaking, training, and coaching in the Senior Living Industry. I have 4 audio files that I want to put to a CD. The names of the CD's are:

1- Leadership - Creating A Culture of Excellence in Senior Living
2- The Purpose of Your Senior Living Business
3- A Leaders Vision - Your Attention Becomes Your Intention
4- Group Interviews -A Secret in Employee Retention

I think I can use the same CD cover for each CD. I just need the same design but 4 different ones with the names above. So everything will be the same but the name change. The inside cover will be I will consider other colors but it would be great if it would look good with the logo. I also need help with designing the CD face itself. I will be using a standard Jewel CD case. I need the front cover, the inside cover, and the back. The logo will be on all three.

On the front:

Part of me thinks it should be a clean simple design with my logo, my picture, and the title. But I am also curious about the picture of me with the elderly lady. - I need the 4 designs that are the same except the title.

On the Inside:

It can be the same design but the wording will be specific to that CD and the 4 insides will be:

All businesses rise and fall with leadership. This is especially true in the senior living industry. The life of that rise or fall is based on the culture the leader creates. Learn the 3 keys to what leaders know and do. Learn what the Importance Factor is and how you can put it to work to create and sustain a winning culture that will drive your business and occupancy above the rest.

What is the purpose of your senior living business? Your understanding to the answer of this question makes all the difference. After you have gained this understanding it takes the right beliefs and behavior of associates to fulfill this purpose. What's the purpose? How is it fulfilled?

They want a captain not a boss. As a leader in senior living you steer the ship. What you put your attention on becomes the intention of your community. Your ability to create a vision, help people embrace that vision, and learn how to stay focused when the storms of the industry come raging, is the key to your success. There is a pattern to achieving this success. Come learn this pattern and how to apply it in your life and your business. It can make all the difference.

A business can not be better than it's people. The right people are the key not just people. Learn where your focus should be to hire the right people. After you hire then find out what you can do to retain them and engage them. If you want happy residents you need happy associates.

On the back it will need to have:

1- My Logo
2- www.LevMarchetti.example
3- Email: info@LevMarchetti.example
4- You could put the picture of me and the elderly lady as a watermark on the back with the above info.

I have a short turn around time and need designs quickly. I also need help with designing the CD. My picture, the logo, and the Title.

```html
<!DOCTYPE html>
<html lang="en">
<head>
<meta charset="utf-8">
<title>Leadership – CD Cover and Disc</title>
<link href="https://fonts.googleapis.com/css2?family=Cinzel:wght@600&family=Nunito+Sans:wght@400;600&display=swap" rel="stylesheet">
<style>
  :root {
    --stage: #5d5d67;
    --gold: #d9c99c;
    --gold-deep: #c6b283;
    --panel: #16191c;
    --panel-2: #22262a;
    --ink-light: #eceae4;
    --ink-soft: #cfcdc6;
    --tab: #e9e9ea;
    --tab-ink: #1b1d20;
    --disc: #141415;
  }
  * { margin: 0; padding: 0; box-sizing: border-box; }
  html, body { width: 1200px; height: 757px; overflow: hidden; }
  body {
    background: var(--stage);
    font-family: "Nunito Sans", Arial, sans-serif;
    position: relative;
  }

  /* Cover */
  .cover {
    position: absolute;
    left: 40px; top: 98px;
    width: 560px; height: 560px;
    background: var(--gold);
  }
  .cover-badge {
    position: absolute;
    right: 8px; top: 0;
    width: 22px; height: 22px;
    border-radius: 50%;
    background: #3d4a78;
    border: 2px solid #e6e2d6;
  }
  .cover-panel {
    position: absolute;
    left: 30px; top: 24px; right: 0; bottom: 16px;
    background: linear-gradient(135deg, var(--panel) 0%, var(--panel-2) 55%, var(--panel) 100%);
    overflow: hidden;
  }
  .headline {
    position: absolute;
    left: 34px; top: 52px;
    color: var(--ink-light);
    font-weight: 600;
    font-size: 18px;
    letter-spacing: 0.06em;
    line-height: 31px;
  }
  .headline span { display: block; }
  .headline .second { padding-left: 47px; }
  .summary {
    position: absolute;
    left: 27px; top: 124px;
    width: 296px;
    color: var(--ink-soft);
    font-size: 10.8px;
    line-height: 13px;
    text-indent: 7px;
  }
  .bio {
    position: absolute;
    left: 27px; top: 208px;
    width: 296px;
    color: var(--ink-soft);
    font-size: 8.9px;
    line-height: 11.3px;
    text-indent: 7px;
  }
  .portrait {
    position: absolute;
    left: 340px; top: 22px;
    width: 138px; height: 452px;
    border-radius: 60px 60px 10px 10px;
    background: linear-gradient(180deg, #5a4a3e 0%, #3a3d44 18%, #2a2d33 60%, #1c1e22 100%);
    opacity: 0.9;
  }
  .title-tab {
    position: absolute;
    left: -30px; top: 320px;
    width: 278px; height: 90px;
    background: linear-gradient(180deg, #f0f0f1, #dcdcde);
    border-radius: 0 12px 12px 0;
    display: flex; align-items: center;
    padding-left: 57px;
  }
  .title-tab h1 {
    font-family: "Cinzel", Georgia, serif;
    font-weight: 600;
    font-size: 28px;
    letter-spacing: 0.09em;
    color: var(--tab-ink);
  }
  .contact {
    position: absolute;
    left: 11px; bottom: 10px;
    display: flex; align-items: center; gap: 8px;
  }
  .contact-mark {
    width: 40px; height: 40px;
    border-radius: 50%;
    background: var(--gold-deep);
  }
  .contact-lines {
    color: var(--gold);
    font-size: 9.6px;
    line-height: 11.6px;
  }

  /* Disc */
  .disc {
    position: absolute;
    left: 620px; top: 113px;
    width: 530px; height: 530px;
  }
  .disc text { font-family: "Nunito Sans", Arial, sans-serif; }
  .disc .disc-title { font-family: "Cinzel", Georgia, serif; font-size: 40px; letter-spacing: 0.12em; fill: #3d3d3f; }
  .disc .disc-tagline { font-size: 16px; fill: var(--gold-deep); letter-spacing: 0.02em; }
  .disc .disc-fine { font-size: 7.5px; fill: #a99b78; }
  .disc .disc-name { font-size: 13px; font-weight: 600; fill: var(--tab-ink); }
</style>
</head>
<body>

<section class="cover" aria-label="CD cover">
  <div class="cover-badge" aria-hidden="true"></div>
  <div class="cover-panel">
    <h2 class="headline">
      <span>All Businesses Rise</span>
      <span class="second">Or Fall With Leadership</span>
    </h2>
    <p class="summary">This is especially true in the senior living industry. The life of that rise or fall is based on the culture the leader creates. Learn the 3 keys to what leaders know and do. Learn what the importance factor is and how you can put it to work to create and sustain a winning culture that will drive your business and occupancy above the rest.</p>
    <p class="bio">Lev Marchetti’s experience in the Senior Living Industry ranges from caregiver to becoming an executive director at the age of 22. He has operated licensed communities from 12 to 250 beds in the assisted living arena. Making lots of mistakes as a young director he has made it his purpose to understand what drives the business and how to create cultures of excellence. He has spent his career transforming troubled communities starting with their culture.</p>
    <div class="portrait" role="img" aria-label="Portrait photo of Lev Marchetti standing in a dark suit"></div>
    <div class="title-tab"><h1>Leadership</h1></div>
    <div class="contact">
      <div class="contact-mark" aria-hidden="true"></div>
      <div class="contact-lines">
        www.LevMarchetti.example<br>
        info@LevMarchetti.example<br>
        Lev Marchetti
      </div>
    </div>
  </div>
</section>

<svg class="disc" viewBox="0 0 530 530" aria-label="CD face">
  <defs>
    <radialGradient id="discShade" cx="40%" cy="35%" r="75%">
      <stop offset="0" stop-color="#2a2a2c"/>
      <stop offset="1" stop-color="#0e0e0f"/>
    </radialGradient>
    <clipPath id="discClip"><circle cx="265" cy="265" r="262"/></clipPath>
    <path id="arcTitle" d="M 90 265 A 175 175 0 0 1 440 265"/>
    <path id="arcTagline" d="M 32 265 A 233 233 0 0 1 498 265"/>
    <path id="arcFine" d="M 55 265 A 210 210 0 0 1 475 265"/>
    <path id="arcUrl" d="M 460 265 A 195 195 0 0 1 70 265"/>
  </defs>
  <circle cx="265" cy="265" r="264" fill="#3a3a3e"/>
  <circle cx="265" cy="265" r="262" fill="url(#discShade)"/>
  <text class="disc-title"><textPath href="#arcTitle" startOffset="50%" text-anchor="middle">LEADERSHIP</textPath></text>
  <text class="disc-tagline"><textPath href="#arcTagline" startOffset="50%" text-anchor="middle">Creating A Culture Of Excellence In Senior Living</textPath></text>
  <text class="disc-fine"><textPath href="#arcFine" startOffset="50%" text-anchor="middle">© 2014 The Marchetti Group, LLC / All Rights Reserved</textPath></text>
  <text class="disc-fine"><textPath href="#arcUrl" startOffset="50%" text-anchor="middle">www.LevMarchetti.example</textPath></text>
  <circle cx="265" cy="265" r="92" fill="none" stroke="#3b3b3e" stroke-width="1.5"/>
  <circle cx="265" cy="265" r="56" fill="var(--gold)"/>
  <circle cx="265" cy="265" r="47" fill="#2b2b2e"/>
  <circle cx="265" cy="265" r="40" fill="#4a4a4f"/>
  <g clip-path="url(#discClip)">
    <rect x="380" y="228" width="160" height="74" rx="12" fill="var(--tab)"/>
  </g>
  <circle cx="400" cy="265" r="6" fill="var(--gold-deep)"/>
  <text class="disc-name" x="412" y="270">Lev Marchetti</text>
</svg>

</body>
</html>
```